Bourbon label design for bourbon brand. Looking to freshen our current label.

I need a Bourbon label design for our rebranded Bourbon bottle. Label should include picture of our horse and our logo on the bottle. Front Label is 3.5 inches wide and 6 inches tall, back label is 4 inches tall and 3 inches wide. Back label can be a simple plain logo like the one in the brief. I have included a design of our current bottle and label. We want to stay close to the current color schemes but want a fresh rebrand of the design. The label needs to be the correct size on a tall bottle like pictured.

Target Market(s)

Our Bourbon members, 30-50 year old males

Requirements
Must have
• Picture of our horse, our B logo , straight Bourbon whiskey on the front. Room to edit text on the back label.

```html
<!DOCTYPE html>
<html lang="en">
<head>
<meta charset="utf-8">
<title>Nightfall Winners Series – Bourbon Labels</title>
<link rel="stylesheet" href="https://fonts.googleapis.com/css2?family=Oswald:wght@400&family=Montserrat:wght@400;700&display=swap">
<style>
  :root {
    --bg-light: #f3e7b4;
    --bg-dark: #d8c08a;
    --label-black: #000000;
    --silver: #c8c8c8;
    --gold: #c9a25a;
    --white: #ffffff;
    --art-light: #8f8f8f;
    --art-mid: #3b3b3b;
  }
  * { box-sizing: border-box; margin: 0; padding: 0; }
  html, body { width: 1200px; height: 1200px; overflow: hidden; }
  body {
    background: radial-gradient(circle at 30% 45%, var(--bg-light), var(--bg-dark));
    font-family: "Montserrat", sans-serif;
    position: relative;
  }
  .display { font-family: "Oswald", sans-serif; font-weight: 400; white-space: nowrap; }

  .label {
    position: absolute;
    top: 255px;
    width: 460px;
    height: 690px;
    background: var(--label-black);
    color: var(--silver);
    text-align: center;
    overflow: hidden;
  }
  .label--front { left: 110px; }
  .label--back { left: 630px; }
  .label--front > * { position: absolute; z-index: 1; }

  .series { display: flex; align-items: center; justify-content: center; gap: 12px; }
  .series__rule { width: 95px; height: 12px; flex: none; }
  .series__title { font-size: 28px; line-height: 1; color: var(--silver); letter-spacing: 0.5px; }
  .label--front .series { left: 0; right: 0; top: 32px; }

  .label--front .horse-art {
    z-index: 0;
    left: 20px; top: 82px; width: 420px; height: 520px;
    background: radial-gradient(ellipse at 50% 42%, var(--art-light) 0%, var(--art-mid) 45%, #111 72%, var(--label-black) 92%);
  }
  .brand-mark {
    left: 0; right: 0; top: 305px;
    display: flex; align-items: center; justify-content: center; gap: 10px;
    font-size: 30px; line-height: 1; color: var(--white);
  }
  .brand-mark__dot { width: 16px; height: 16px; border-radius: 50%; background: var(--white); }
  .brand-name {
    left: 0; right: 0; top: 362px;
    font-size: 82px; line-height: 1; color: var(--silver); letter-spacing: 1px;
  }
  .product-type {
    left: 0; right: 0; top: 468px;
    font-size: 24px; line-height: 1; color: var(--silver);
  }
  .stat { color: var(--gold); line-height: 1; text-align: center; }
  .stat small { display: block; color: var(--silver); font-size: 13px; margin-top: 2px; }
  .stat--abv { left: 48px; top: 512px; font-size: 28px; }
  .stat--age { right: 48px; top: 512px; font-size: 28px; }
  .stat--left { left: 36px; top: 584px; font-size: 24px; line-height: 1.05; }
  .stat--right { right: 36px; top: 584px; font-size: 24px; line-height: 1.05; }
  .volume { left: 0; right: 0; top: 648px; font-size: 17px; line-height: 1; color: var(--silver); }

  /* back label */
  .back-art {
    width: 150px; height: 110px; margin: 22px auto 0;
    background: radial-gradient(ellipse at 50% 50%, #9a9a9a 0%, #3a3a3a 55%, var(--label-black) 100%);
  }
  .back-brand {
    margin-top: 4px; display: flex; align-items: center; justify-content: center; gap: 8px;
    font-size: 34px; color: var(--silver); line-height: 1;
  }
  .back-brand__dot { width: 11px; height: 11px; border-radius: 50%; background: var(--silver); }
  .back-brand-sub { font-size: 30px; color: var(--silver); line-height: 1.05; }
  .company-line { display: flex; align-items: center; justify-content: center; gap: 14px; margin-top: 2px; }
  .company-line__rule { width: 80px; height: 1px; background: var(--gold); }
  .company-line__text { font-size: 7px; letter-spacing: 4px; color: var(--silver); }
  .back-series { margin-top: 10px; }
  .back-series .series__title { font-size: 19px; }
  .back-series .series__rule { width: 70px; height: 10px; }
  .edition { font-size: 17px; color: var(--white); line-height: 1.3; margin-top: 2px; }
  .story { font-size: 11.5px; line-height: 1.5; color: var(--white); margin: 10px 30px 0; }
  .story strong { font-weight: 700; }
  .bottler { font-size: 11.5px; line-height: 1.5; color: var(--white); margin-top: 12px; }
  .website { font-size: 20px; color: var(--white); margin-top: 8px; line-height: 1.2; }
  .back-volume { font-size: 16px; color: var(--white); margin-top: 4px; line-height: 1.2; }
  .warning {
    font-size: 7.5px; line-height: 1.55; color: var(--white); text-align: justify;
    margin: 6px 78px 0; letter-spacing: 0.4px;
  }
  .warning strong { font-weight: 700; letter-spacing: 1px; }
</style>
</head>
<body>

<section class="label label--front" aria-label="Front label">
  <div class="horse-art" role="img" aria-label="Black and white painted illustration of the racehorse with jockey charging forward, splattered ink"></div>
  <div class="series">
    <svg class="series__rule" viewBox="0 0 95 12"><g stroke="#c9a25a" stroke-width="1.3"><line x1="0" y1="2" x2="95" y2="2"/><line x1="20" y1="6" x2="95" y2="6"/><line x1="10" y1="10" x2="95" y2="10"/></g></svg>
    <span class="series__title display">WINNERS SERIES</span>
    <svg class="series__rule" viewBox="0 0 95 12"><g stroke="#c9a25a" stroke-width="1.3"><line x1="0" y1="2" x2="95" y2="2"/><line x1="0" y1="6" x2="75" y2="6"/><line x1="0" y1="10" x2="85" y2="10"/></g></svg>
  </div>
  <div class="brand-mark display"><span class="brand-mark__dot"></span>NIGHTFALL</div>
  <div class="brand-name display">NIGHTFALL</div>
  <div class="product-type display">STRAIGHT BOURBON WHISKEY</div>
  <div class="stat stat--abv display">66%<small>ALC/VOL</small></div>
  <div class="stat stat--age display">12<small>YEARS</small></div>
  <div class="stat stat--left display">SINGLE<br>BARREL</div>
  <div class="stat stat--right display">BARREL<br>STRAIGHT</div>
  <div class="volume display">750 ML</div>
</section>

<section class="label label--back" aria-label="Back label">
  <div class="back-art" role="img" aria-label="Small black and white illustration of the racehorse and jockey"></div>
  <div class="back-brand display"><span class="back-brand__dot"></span>NIGHTFALL</div>
  <div class="back-brand-sub display">BARREL</div>
  <div class="company-line">
    <span class="company-line__rule"></span><span class="company-line__text">COMPANY</span><span class="company-line__rule"></span>
  </div>
  <div class="series back-series">
    <svg class="series__rule" viewBox="0 0 70 10"><g stroke="#c9a25a" stroke-width="1.2"><line x1="0" y1="1.5" x2="70" y2="1.5"/><line x1="12" y1="5" x2="70" y2="5"/><line x1="6" y1="8.5" x2="70" y2="8.5"/></g></svg>
    <span class="series__title display">WINNERS SERIES</span>
    <svg class="series__rule" viewBox="0 0 70 10"><g stroke="#c9a25a" stroke-width="1.2"><line x1="0" y1="1.5" x2="70" y2="1.5"/><line x1="0" y1="5" x2="58" y2="5"/><line x1="0" y1="8.5" x2="64" y2="8.5"/></g></svg>
  </div>
  <p class="edition display">SILVER TEMPEST EDITION<br>SINGLE BARREL Nº45</p>
  <p class="story">The Nightfall Racing Winners Series honors the horses who have brought home victories for our stable. This editions celebrates<br><strong>Silver Tempest</strong><br>and her maiden victory on May 28, 2021. Raise a glass to her incredible career with this non chill filtered single barrel crafted in her honor.<br>Here’s to <strong>Silver Tempest</strong> - a true champions!</p>
  <p class="bottler">Bottled by Old Riverbend Whiskey Co., Louisville Kentucky<br>Distilled in Bardstown, Kentucky</p>
  <p class="website display">NIGHTFALL-GROUP. COM</p>
  <p class="back-volume display">750 ML</p>
  <p class="warning"><strong>GOVERNMENT WARNING:</strong> (1) According to the Surgeon General, women should not drink alcoholic beverages during pregnancy because of the risk of birth defects. (2) Consumption of alcoholic beverages impairs your ability to drive a car or operate machinery, and may cause health problems.</p>
</section>

</body>
</html>
```